Computer consultant business card

Bexil Software is a newly started computer consulting company. It's a small one-man company that provides mostly Vornix applications but also websites in collaboration with designers. I'm running this company on the side of full time university studies.

I want the final design to be clean and memorable. Be creative! :)

Some inspiration:
http://www.pixelmarta.com/design/48317
http://www.pixelmarta.com/design/2739164/business-card-design-by-frostlynk
http://www.pixelmarta.com/design/604281/business-card-design-by-koralind-vestrabanu

See attachment for my company logo.
Updates

I would like to thank everyone for submitting! I'll need a couple of days to review and ultimately select a design.

Target Market(s)

Non-technical entrepreneurs and small companies.

Industry/Entity Type

University

Requirements
Must have
• My company logo.
In any way, both colors from my logo.
First- and last name, e-mail and phone number.
Double-sided design.
Nice to have
• Something creative with the symbol in my logo

```html
<!DOCTYPE html>
<html lang="en">
<head>
<meta charset="utf-8">
<title>Bexil Software – Business Card</title>
<link rel="stylesheet" href="https://fonts.googleapis.com/css2?family=Arimo:wght@400;700&display=swap">
<style>
  :root {
    --brand-blue: #2379f6;
    --brand-dark: #333131;
    --card-white: #ffffff;
    --rule-grey: #6f6f6f;
    --stage: #e9e9e9;
    --text: #222222;
  }
  * { box-sizing: border-box; margin: 0; padding: 0; }
  html, body {
    width: 1200px; height: 820px; overflow: hidden;
    background: var(--stage);
    font-family: "Arimo", Arial, sans-serif;
  }
  .sheet { position: relative; width: 1200px; height: 820px; }
  .card {
    position: absolute; width: 640px; height: 366px;
    background: var(--card-white);
    box-shadow: 0 2px 8px rgba(0,0,0,0.18);
    overflow: hidden;
  }
  .card--front { left: 80px; top: 24px; }
  .card--back { left: 480px; top: 430px; }

  /* front */
  .name-band {
    position: absolute; left: 0; right: 0; top: 44px; height: 80px;
    border-top: 2px solid var(--rule-grey);
    border-bottom: 2px solid var(--rule-grey);
    padding: 5px 0;
  }
  .name-band__fill {
    height: 100%; background: var(--brand-blue);
    display: flex; align-items: center; justify-content: center;
    color: var(--card-white); font-size: 22px;
  }
  .name-band__first { font-weight: 700; margin-right: 6px; }
  .name-band__last { font-weight: 400; font-size: 18px; }

  .front-mark {
    position: absolute; left: 96px; top: 188px;
    display: flex; align-items: center; gap: 14px;
    color: var(--brand-dark); font-size: 46px; font-weight: 700;
  }
  .mark-dot {
    width: 34px; height: 34px; border-radius: 50%;
    background: var(--brand-blue);
  }
  .divider {
    position: absolute; left: 338px; top: 160px; width: 3px; height: 150px;
    background: linear-gradient(to bottom, #d0d0d0, #8a8a8a 60%, #d0d0d0);
  }
  .contact {
    position: absolute; left: 360px; top: 172px;
    color: var(--text); font-size: 15px; line-height: 20px;
  }
  .contact__address { margin-bottom: 16px; }
  .contact__line { display: flex; align-items: center; gap: 8px; margin-bottom: 8px; }
  .contact__icon { width: 13px; height: 13px; flex: none; }

  /* back */
  .back-mark {
    position: absolute; inset: 0;
    display: flex; align-items: center; justify-content: center; gap: 26px;
    color: var(--brand-dark); font-size: 104px; font-weight: 700;
    letter-spacing: 2px;
  }
  .back-mark .mark-dot { width: 96px; height: 96px; }
</style>
</head>
<body>
<main class="sheet">
  <section class="card card--front" aria-label="Card front">
    <div class="name-band">
      <div class="name-band__fill">
        <span class="name-band__first">First Name,</span>
        <span class="name-band__last">Last Name</span>
      </div>
    </div>

    <div class="front-mark">
      <span class="mark-dot"></span>
      <span>bexil</span>
    </div>

    <div class="divider"></div>

    <div class="contact">
      <p class="contact__address">14, Harlow Court<br>Marlin, State 0731</p>
      <p class="contact__line">
        <svg class="contact__icon" viewBox="0 0 16 16" aria-hidden="true">
          <circle cx="8" cy="8" r="7" fill="none" stroke="#2379f6" stroke-width="1.6"/>
          <path d="M5.5 4.5c-.8.8-.6 2.6 1 4.4s3.6 2.3 4.4 1.5l-1.3-1.4-1 .5-2-2 .5-1z" fill="#2379f6"/>
        </svg>
        <span>0912 487630</span>
      </p>
      <p class="contact__line">
        <svg class="contact__icon" viewBox="0 0 16 16" aria-hidden="true">
          <circle cx="8" cy="8" r="8" fill="#2379f6"/>
          <rect x="3.5" y="5" width="9" height="6" fill="#fff"/>
          <path d="M3.5 5l4.5 3.5L12.5 5" fill="none" stroke="#2379f6" stroke-width="1"/>
        </svg>
        <span>info@bexil.com</span>
      </p>
    </div>
  </section>

  <section class="card card--back" aria-label="Card back">
    <div class="back-mark">
      <span class="mark-dot"></span>
      <span>bexil</span>
    </div>
  </section>
</main>
</body>
</html>
```